VFX Company Business Card Design Project

The Kestrel Works is a decentralized Visual Effects Studio servicing the television and feature film industries.
Project Brief:
Take our logo that was previously designed on Pencil Harbor and make a double sided business card.
Requirements:
- Card MUST be double sided.
- Front of card MUST have the yellow part of our logo against the dark grey background.
- Back of card is completely up to the designer.
- Back of card must include the complete company logo.
Please follow these File Preparation guidelines:
http://printnook.ca/infopage?file=filetype_en&s=PrintNook_new&lang=en
Business

```html
<!DOCTYPE html>
<html lang="en">
<head>
<meta charset="utf-8">
<title>The Kestrel Works – Business Card</title>
<link rel="stylesheet" href="https://fonts.googleapis.com/css2?family=Asap:wght@400;500&display=swap">
<style>
  :root {
    --backdrop: #7d939c;
    --card: #333333;
    --accent: #f6c51c;
    --ink: #ececec;
    --ink-soft: #d6d6d6;
  }
  * { margin: 0; padding: 0; box-sizing: border-box; }
  html, body {
    width: 1200px; height: 960px; overflow: hidden;
    background: var(--backdrop);
    font-family: "Asap", Arial, sans-serif;
  }
  .canvas {
    position: relative; width: 1200px; height: 960px;
  }
  .card {
    position: absolute; left: 250px;
    width: 700px; height: 400px;
    background: var(--card);
    border-radius: 3px;
    box-shadow: 0 10px 28px rgba(0,0,0,.28);
  }
  .card--info { top: 60px; }
  .card--front { top: 500px; display: flex; align-items: center; justify-content: center; }

  .brand {
    position: absolute; left: 48px; top: 46px;
    display: flex; align-items: center; gap: 16px;
  }
  .brand__dot {
    width: 44px; height: 44px; border-radius: 50%;
    border: 6px solid var(--accent);
  }
  .brand__name {
    color: var(--accent); font-size: 40px; font-weight: 500; letter-spacing: .5px;
  }

  .person { position: absolute; left: 80px; top: 208px; }
  .person__name { color: var(--accent); font-size: 30px; font-weight: 400; letter-spacing: .5px; }
  .person__role { color: var(--ink); font-size: 17px; margin-top: 4px; }

  .contact { position: absolute; left: 330px; top: 188px; color: var(--ink); font-size: 17px; }
  .contact__row { display: flex; gap: 18px; line-height: 24px; }
  .contact__label { color: var(--accent); width: 10px; font-size: 14px; }
  .contact__address { margin-top: 30px; line-height: 24px; color: var(--ink-soft); }

  .front-mark { display: flex; align-items: center; gap: 24px; }
  .front-mark__dot {
    width: 76px; height: 76px; border-radius: 50%;
    border: 12px solid var(--accent);
  }
  .front-mark__name { color: var(--accent); font-size: 58px; font-weight: 500; }
</style>
</head>
<body>
<main class="canvas">
  <section class="card card--info" aria-label="Card back with contact details">
    <div class="brand">
      <span class="brand__dot"></span>
      <span class="brand__name">The Kestrel Works</span>
    </div>
    <div class="person">
      <p class="person__name">MARTEN HALE</p>
      <p class="person__role">Managing Partner</p>
    </div>
    <div class="contact">
      <p class="contact__row"><span class="contact__label">t</span>(480) 555-0143</p>
      <p class="contact__row"><span class="contact__label">e</span>name@kestrelworks.com</p>
      <p class="contact__row"><span class="contact__label">w</span>www.kestrelworks.com</p>
      <p class="contact__address">5678 West Harbor Lane,<br>Suite 210, Lakeview</p>
    </div>
  </section>

  <section class="card card--front" aria-label="Card front">
    <div class="front-mark">
      <span class="front-mark__dot"></span>
      <span class="front-mark__name">The Kestrel Works</span>
    </div>
  </section>
</main>
</body>
</html>
```